Facefolio & Instagram Design for: The Ledger of Pim - Paws of Quiet Hound

Need a Facefolio Page and Instagram Page too for helping launch a book as a brand new author with a book on my old dog Pim and the Zen lessons he taught me.
Its all for folks who love dogs and especially rescue dog stories
Its all for folks who are interested in something slightly spiritual and for self growth
I attach the review copy from my publishers who are standing up a website but recommend a Facefolio Page that is attached to my own personal one and an Instagram Page
I intend on publishing weekly "Pimtricks" (The dog was called Pim)
I intend on posting Zen talks (in lay man's terms)
I have a second book being written to follow on the one
Myself as an Author needs profiling
The book needs ALOT of promotion - and we can't travel!
I need to host a bunch of "book talks/launches"
Need to send folks to my website to by the book: Hard/Paperback/Lumera - which comes with book trailer
I have hundreds of photos to give
I have alot of sketches of the dog to share which did not make it into the book
My competition are books like:
Hollis & Us
A Cat naps int Caring Lodge
Tuxa
The Baron's Beagle
A Pups Journey
Need this ASAP - publishing date is moved up to October 2021!
Link t Author hot File Crate: https://www.filecrate.example/sh/kqwplm2231907t4/AAFhtrWmnPqLsKe7vb_XoPla?dl=0
Link to Dog Photos:
https://www.filecrate.example/sh/mvbtr83knwoz02/AAC4j1hnqe_k5Rs9WYpoltQ2m?dl=0
Updates
Hello, I will be in hospitaal having surgery on my neck and request tow more days to =make any kind of small changes. Thank you Marisol
Target Market(s)
Dog owners around the world, especially those wth rescue dogs and those looking for personal growth and those interested in Zen Buddhism
Industry/Entity Type
Author promoting soon to be published book/s
Requirements
Must have
- Author Photo/E-Mail Sign Up/Link to Instagram (see brief to design this)/Link to upcoming website/Link to Writer Hub (might need to design me something)/Photo Gallery
Nice to have
- Author features and Dog Images (I have new dogs we can show)
Should not have
- Cute - its a meaningful book

```html
<!DOCTYPE html>
<html lang="en">
<head>
<meta charset="utf-8">
<title>The Ledger of Pim – Facefolio Cover and Page View</title>
<link rel="stylesheet" href="https://fonts.googleapis.com/css2?family=Montserrat:wght@500;600;700;900&family=Kalam:wght@400&family=Great+Vibes&family=Raleway:wght@500&family=Libre+Baskerville&family=Noto+Sans:wght@400;600;700&display=swap">
<style>
  :root {
    --page-bg: #eceef2;
    --label-blue: #1f55b4;
    --title-blue: #0a97d6;
    --quote-slate: #4b5f86;
    --script-ink: #2d3550;
    --band-purple: #5a3ec8;
    --ring-purple: #5b2fc2;
    --sky-top: #cdc3ec;
    --sky-mid: #e2e7f3;
    --sky-low: #b8c8dc;
    --ui-blue: #1877f2;
    --ui-text: #050505;
    --ui-muted: #65676b;
    --ui-chip: #e4e6eb;
    --ui-line: #ced0d4;
    --ui-feed: #f0f2f5;
    --notice-grey: #8a8d93;
    --white: #ffffff;
  }
  * { margin: 0; padding: 0; box-sizing: border-box; }
  html, body { width: 1200px; height: 1200px; overflow: hidden; background: var(--page-bg); }
  body { position: relative; font-family: "Noto Sans", sans-serif; color: var(--ui-text); }
  .abs { position: absolute; }

  /* vertical board labels */
  .board-label {
    position: absolute; writing-mode: vertical-rl; transform: rotate(180deg);
    font-family: "Montserrat", sans-serif; font-weight: 500; color: var(--label-blue);
    white-space: nowrap; line-height: 1;
  }
  .label-cover { left: 36px; top: 72px; font-size: 30px; }
  .label-page { left: 58px; top: 588px; font-size: 47px; z-index: 3; }

  /* cover artwork, native size 996 x 368 */
  .cover-art {
    position: relative; width: 996px; height: 368px; overflow: hidden;
    background: linear-gradient(180deg, var(--sky-top) 0%, var(--sky-mid) 48%, var(--sky-low) 100%);
  }
  .author-photo {
    position: absolute; left: 0; top: 0; width: 560px; height: 368px;
    background:
      radial-gradient(ellipse at 38% 48%, #c2345e 0%, #8c2447 34%, rgba(120,40,90,0) 68%),
      linear-gradient(90deg, #3a2a55 0%, #6b4a6a 48%, rgba(200,200,225,0) 100%);
  }
  .ring { position: absolute; left: 0; top: 0; }
  .coming-soon {
    position: absolute; left: 49px; top: 240px; display: flex; align-items: baseline;
    color: var(--white); line-height: 1; text-shadow: 0 2px 6px rgba(0,0,0,.35); white-space: nowrap;
  }
  .coming-soon .plain { font-family: "Raleway", sans-serif; font-weight: 500; font-size: 44px; }
  .coming-soon .script { font-family: "Great Vibes", cursive; font-size: 86px; margin-left: 4px; }
  .title-row {
    position: absolute; right: 49px; top: 26px; display: flex; align-items: baseline; gap: 14px;
    font-family: "Montserrat", sans-serif; font-weight: 900; color: var(--title-blue);
    white-space: nowrap; line-height: 1;
  }
  .title-lead { font-size: 36px; }
  .title-name { font-size: 104px; letter-spacing: -2px; }
  .subtitle {
    position: absolute; left: 450px; width: 520px; top: 122px; text-align: center;
    font-family: "Kalam", cursive; font-size: 46px; color: var(--script-ink); line-height: 1.3;
  }
  .tagline {
    position: absolute; left: 481px; top: 200px; width: 460px; text-align: center;
    font-family: "Montserrat", sans-serif; font-weight: 700; font-size: 18px; line-height: 28px;
    color: var(--quote-slate); text-transform: uppercase; white-space: nowrap;
  }
  .retailers {
    position: absolute; left: 455px; top: 293px; width: 541px; height: 46px;
    background: var(--band-purple); display: flex; align-items: center; justify-content: space-around;
    color: var(--white);
  }
  .retailer { font-family: "Libre Baskerville", serif; font-size: 16px; white-space: nowrap; }

  /* board top: cover on its own */
  .cover-showcase { position: absolute; left: 121px; top: 29px; box-shadow: 0 3px 10px rgba(0,0,0,.25); }

  /* unpublished notice */
  .notice-bar {
    position: absolute; left: 0; top: 448px; width: 1200px; height: 46px; background: var(--notice-grey);
    display: flex; align-items: center; color: var(--white); font-size: 12px;
  }
  .notice-bar .caret { margin: 0 8px 0 0; width: 0; height: 0; border-left: 5px solid var(--white); border-top: 4px solid transparent; border-bottom: 4px solid transparent; }
  .publish-btn {
    position: absolute; left: 1054px; top: 9px; width: 133px; height: 28px; border-radius: 5px;
    background: var(--ui-blue); color: var(--white); font-weight: 600; font-size: 12px;
    display: flex; align-items: center; justify-content: center;
  }

  /* page view */
  .page-view { position: absolute; left: 0; top: 494px; width: 1200px; height: 682px; overflow: hidden; background: var(--ui-feed); }
  .page-header-bg {
    position: absolute; left: 0; top: 0; width: 1200px; height: 442px;
    background: linear-gradient(180deg, #6a5cbf 0%, #b3a9dd 24%, #ffffff 58%);
    border-bottom: 1px solid var(--ui-line);
  }
  .page-header-bg .right-sky {
    position: absolute; right: 0; top: 0; width: 241px; height: 442px;
    background: linear-gradient(180deg, #a9c1e0 0%, #d6e1ef 35%, #ffffff 60%);
  }
  .page-header-bg .centre { position: absolute; left: 207px; top: 0; width: 752px; height: 442px; background: var(--white); }
  .page-cover { position: absolute; left: 207px; top: 1px; width: 752px; height: 278px; overflow: hidden; border-radius: 0 0 7px 7px; }
  .page-cover .cover-art { transform: scale(.755); transform-origin: 0 0; }
  .edit-cover {
    position: absolute; left: 875px; top: 238px; width: 58px; height: 28px; border-radius: 5px;
    background: var(--white); font-size: 12px; display: flex; align-items: center; justify-content: center; gap: 4px;
  }

  .avatar {
    position: absolute; border-radius: 50%; background: var(--white); border: 1px solid var(--ui-line);
    display: flex; align-items: center; justify-content: center; text-align: center;
    font-family: "Montserrat", sans-serif; font-weight: 700; color: var(--label-blue); line-height: 1.05;
  }
  .avatar-main { left: 236px; top: 269px; width: 106px; height: 106px; font-size: 13px; border: 4px solid var(--white); box-shadow: 0 0 0 1px var(--ui-line); }
  .avatar-cam {
    position: absolute; left: 312px; top: 348px; width: 28px; height: 28px; border-radius: 50%;
    background: var(--ui-chip); display: flex; align-items: center; justify-content: center;
  }
  .page-name { position: absolute; left: 364px; top: 312px; font-size: 21px; font-weight: 700; }
  .page-handle { position: absolute; left: 364px; top: 343px; font-size: 13px; color: var(--ui-muted); }
  .page-handle b { color: var(--ui-blue); font-weight: 600; }
  .btn {
    position: absolute; border-radius: 5px; background: var(--ui-chip); font-size: 13px; font-weight: 600;
    display: flex; align-items: center; justify-content: center; gap: 6px;
  }
  .btn-shop { left: 684px; top: 339px; width: 249px; height: 31px; }
  .header-rule { position: absolute; left: 233px; top: 393px; width: 700px; height: 1px; background: var(--ui-line); }
  .tabs { position: absolute; left: 233px; top: 394px; height: 48px; display: flex; font-size: 12px; font-weight: 600; color: var(--ui-muted); }
  .tab { padding: 0 12px; display: flex; align-items: center; }
  .tab.active { color: var(--ui-blue); border-bottom: 3px solid var(--ui-blue); }
  .btn-promote { left: 715px; top: 404px; width: 128px; height: 28px; background: var(--ui-blue); color: var(--white); }
  .btn-search { left: 850px; top: 404px; width: 38px; height: 28px; }
  .btn-more { left: 895px; top: 404px; width: 38px; height: 28px; }

  .card { position: absolute; background: var(--white); border-radius: 7px; box-shadow: 0 1px 2px rgba(0,0,0,.15); }
  .setup-card { left: 233px; top: 456px; width: 287px; height: 240px; padding: 14px 13px; }
  .setup-card h2 { font-size: 16px; font-weight: 700; line-height: 20px; }
  .setup-card p { font-size: 12.5px; line-height: 16px; margin-top: 3px; color: var(--ui-text); }
  .setup-card .steps { font-size: 10px; color: var(--ui-muted); margin-top: 5px; }
  .progress { display: flex; gap: 4px; margin-top: 4px; }
  .progress span { flex: 1; height: 6px; border-radius: 3px; background: var(--ui-chip); }
  .progress span.done { background: var(--ui-blue); }
  .setup-row { border-top: 1px solid var(--ui-line); margin-top: 12px; padding-top: 9px; position: relative; }
  .setup-row small { display: block; font-size: 10px; color: var(--ui-muted); }
  .setup-row strong { display: block; font-size: 13px; font-weight: 400; margin-top: 2px; }
  .setup-row svg { position: absolute; right: 6px; top: 20px; }
  .setup-row + .setup-row { margin-top: 8px; }

  .post-card { left: 534px; top: 456px; width: 399px; height: 92px; }
  .post-avatar { left: 12px; top: 10px; width: 28px; height: 28px; font-size: 6px; }
  .create-post { position: absolute; left: 51px; top: 9px; width: 338px; height: 31px; border-radius: 5px; background: var(--ui-chip); font-size: 13px; font-weight: 600; display: flex; align-items: center; justify-content: center; }
  .post-actions { position: absolute; left: 28px; top: 52px; display: flex; gap: 26px; font-size: 12px; color: var(--ui-muted); font-weight: 600; }
  .post-actions span { display: flex; align-items: center; gap: 6px; }
  .dot { width: 14px; height: 14px; border-radius: 50%; display: inline-block; }
  .sq { width: 14px; height: 13px; border-radius: 2px; display: inline-block; }

  .create-card { left: 534px; top: 560px; width: 399px; height: 55px; display: flex; align-items: center; gap: 8px; padding-left: 12px; font-size: 12px; }
  .chip { height: 28px; border-radius: 14px; background: var(--ui-chip); display: flex; align-items: center; gap: 5px; padding: 0 10px; font-weight: 400; }
  .chip i { width: 11px; height: 10px; background: var(--ui-text); border-radius: 2px; display: inline-block; }
  .chip.round i { border-radius: 50%; }
  .pinned-label { position: absolute; left: 534px; top: 640px; font-size: 12px; color: var(--ui-muted); }
  .pinned-card { left: 534px; top: 664px; width: 399px; height: 40px; padding: 10px 0 0 50px; font-size: 12px; font-weight: 600; }

  .compose-fab {
    position: absolute; left: 1149px; top: 633px; width: 38px; height: 38px; border-radius: 50%;
    background: var(--white); box-shadow: 0 2px 8px rgba(0,0,0,.2); display: flex; align-items: center; justify-content: center;
  }
</style>
</head>
<body>

  <div class="board-label label-cover">COVER FACEFOLIO</div>

  <section class="cover-showcase" aria-label="Cover artwork: The Ledger of Pim">
    <div class="cover-art">
      <div class="author-photo" role="img" aria-label="Photo of the author in a red coat kneeling beside her rescue dog Pim"></div>
      <svg class="ring" width="996" height="368" viewBox="0 0 996 368" aria-hidden="true">
        <path d="M98 87 A200 200 0 1 1 420 321" fill="none" stroke="var(--ring-purple)" stroke-width="12" stroke-linecap="round" opacity=".85"/>
      </svg>
      <div class="coming-soon"><span class="plain">Coming</span><span class="script">Soon</span></div>
      <div class="title-row"><span class="title-lead">THE LEDGER OF</span><span class="title-name">PIM</span></div>
      <div class="subtitle">Paws of Quiet Hound</div>
      <p class="tagline">“ All true stories of a rescue<br>dog teaching his owner the<br>real meaning of zen ”</p>
      <div class="retailers">
        <span class="retailer">Writer Hub</span>
        <span class="retailer">Pagewell</span>
        <span class="retailer">Fenwick &amp; Rowe</span>
        <span class="retailer">Harbor Books</span>
      </div>
    </div>
  </section>

  <div class="notice-bar">
    <span class="caret"></span>
    <span>This Page isn't visible. You can publish it when you're ready for people to see it.</span>
    <span class="publish-btn">Publish Page</span>
  </div>

  <section class="page-view" aria-label="Page as seen by the admin">
    <div class="page-header-bg"><div class="right-sky"></div><div class="centre"></div></div>

    <div class="page-cover">
      <div class="cover-art">
        <div class="author-photo" role="img" aria-label="Photo of the author in a red coat kneeling beside her rescue dog Pim"></div>
        <svg class="ring" width="996" height="368" viewBox="0 0 996 368" aria-hidden="true">
          <path d="M98 87 A200 200 0 1 1 420 321" fill="none" stroke="var(--ring-purple)" stroke-width="12" stroke-linecap="round" opacity=".85"/>
        </svg>
        <div class="coming-soon"><span class="plain">Coming</span><span class="script">Soon</span></div>
        <div class="title-row"><span class="title-lead">THE LEDGER OF</span><span class="title-name">PIM</span></div>
        <div class="subtitle">Paws of Quiet Hound</div>
        <p class="tagline">“ All true stories of a rescue<br>dog teaching his owner the<br>real meaning of zen ”</p>
        <div class="retailers">
          <span class="retailer">Writer Hub</span>
          <span class="retailer">Pagewell</span>
          <span class="retailer">Fenwick &amp; Rowe</span>
          <span class="retailer">Harbor Books</span>
        </div>
      </div>
    </div>
    <div class="edit-cover">
      <svg width="13" height="11" viewBox="0 0 13 11" aria-hidden="true"><rect x="0.5" y="2" width="12" height="8.5" rx="1.5" fill="#050505"/><rect x="4" y="0.5" width="5" height="2.5" fill="#050505"/><circle cx="6.5" cy="6.2" r="2.3" fill="#fff"/></svg>Edit
    </div>

    <div class="avatar avatar-main">The Ledger<br>of Pim</div>
    <div class="avatar-cam">
      <svg width="13" height="11" viewBox="0 0 13 11" aria-hidden="true"><rect x="0.5" y="2" width="12" height="8.5" rx="1.5" fill="#050505"/><rect x="4" y="0.5" width="5" height="2.5" fill="#050505"/><circle cx="6.5" cy="6.2" r="2.3" fill="#e4e6eb"/></svg>
    </div>
    <div class="page-name">Test2</div>
    <div class="page-handle"><b>Create @username</b> · Book</div>
    <div class="btn btn-shop">
      <svg width="12" height="12" viewBox="0 0 12 12" aria-hidden="true"><path d="M1 11 L2 8 L8.5 1.5 L10.5 3.5 L4 10 Z" fill="#050505"/></svg>Edit Shop on Website
    </div>

    <div class="header-rule"></div>
    <nav class="tabs">
      <span class="tab active">Home</span><span class="tab">About</span><span class="tab">Events</span><span class="tab">Reviews</span><span class="tab">More ▾</span>
    </nav>
    <div class="btn btn-promote">
      <svg width="14" height="12" viewBox="0 0 14 12" aria-hidden="true"><path d="M1 4 H4 L11 1 V11 L4 8 H1 Z" fill="#fff"/><rect x="3" y="8" width="2.5" height="3.5" fill="#fff"/></svg>Promote
    </div>
    <div class="btn btn-search">
      <svg width="14" height="14" viewBox="0 0 14 14" aria-hidden="true"><circle cx="6" cy="6" r="4.5" fill="none" stroke="#050505" stroke-width="1.6"/><path d="M9.5 9.5 L13 13" stroke="#050505" stroke-width="1.6"/></svg>
    </div>
    <div class="btn btn-more">
      <svg width="14" height="4" viewBox="0 0 14 4" aria-hidden="true"><circle cx="2" cy="2" r="1.5" fill="#050505"/><circle cx="7" cy="2" r="1.5" fill="#050505"/><circle cx="12" cy="2" r="1.5" fill="#050505"/></svg>
    </div>

    <article class="card setup-card">
      <h2>Set your Page up for success</h2>
      <p>Finish setting up your Page so people on Facefolio know that you're a credible business.</p>
      <div class="steps">8 of 13 steps completed</div>
      <div class="progress">
        <span class="done"></span><span class="done"></span><span class="done"></span><span class="done"></span><span class="done"></span><span class="done"></span><span class="done"></span><span class="done"></span><span></span><span></span><span></span><span></span><span></span>
      </div>
      <div class="setup-row">
        <small>Completed</small><strong>Establish your Page's identity</strong>
        <svg width="12" height="8" viewBox="0 0 12 8" aria-hidden="true"><path d="M1 1 L6 6 L11 1" fill="none" stroke="#65676b" stroke-width="2"/></svg>
      </div>
      <div class="setup-row">
        <small>4 steps left</small><strong>Provide info and preferences</strong>
        <svg width="12" height="8" viewBox="0 0 12 8" aria-hidden="true"><path d="M1 1 L6 6 L11 1" fill="none" stroke="#65676b" stroke-width="2"/></svg>
      </div>
    </article>

    <article class="card post-card">
      <div class="avatar post-avatar">Pim</div>
      <div class="create-post">Create Post</div>
      <div class="post-actions">
        <span><i class="sq" style="background:#45bd62"></i>Photo/Video</span>
        <span><i class="dot" style="background:#1877f2"></i>Get Messages</span>
        <span><i class="dot" style="background:#f7b928"></i>Feeling/Activity</span>
      </div>
    </article>

    <article class="card create-card">
      <span>Create</span>
      <span class="chip"><i></i>Live</span>
      <span class="chip"><i></i>Event</span>
      <span class="chip"><i></i>Job</span>
      <span class="chip round"><i></i>Offer</span>
      <span class="chip">···</span>
    </article>

    <div class="pinned-label">PINNED POST</div>
    <article class="card pinned-card">Test2</article>

    <div class="compose-fab">
      <svg width="16" height="16" viewBox="0 0 16 16" aria-hidden="true"><rect x="1" y="3" width="11" height="12" rx="2" fill="none" stroke="#050505" stroke-width="1.6"/><path d="M6 10 L7 7 L13 1 L15 3 L9 9 Z" fill="#050505"/></svg>
    </div>
  </section>

  <div class="board-label label-page">Page from admin view</div>

</body>
</html>
```